BUSINESS CARD - HALLORAN FIELD SERVICES

I would like to create a business card for my fertilizer spreading business. I would like to incorporate my existing logo and also a description of the services offered. The business card will be given to farmers so must be kept simple but effective. It will also be left in stores so much also be eye catching in order to stand out from other cards.

Target Market(s)

FARMERS

Requirements
Must have
• FRONT OF CARD = EXISTING LOGO + "CUSTOMISED SPREADING" below the logo

REAR Of CARD = SERVICES OFFERED AND CONTACT DETAILS

- Bulk fertilizer including Lime, Gypsum, Manure & Compost
- Granular fertilizer including Single Super, Urea, Gran-am, & Custom Blends
- Modern equipment - Autosteer & Variable Rate Capable
- Friendly & Reliable Service
- Contact Gus: 0417 552 308
Nice to have
• utilize same color scheme as existing logo

```html
<!DOCTYPE html>
<html lang="en">
<head>
<meta charset="utf-8">
<title>Halloran Field Services – Business Card</title>
<link href="https://fonts.googleapis.com/css2?family=Arimo:wght@400;700&display=swap" rel="stylesheet">
<style>
  :root {
    --backdrop: #262626;
    --backdrop-edge: #141414;
    --card: #0d0d0d;
    --card-edge: #1c1c1c;
    --text-grey: #a3a3a3;
    --mark-grey: #6b6b6b;
    --accent: #f7941d;
    --rule: #4a4a4a;
  }
  * { box-sizing: border-box; margin: 0; padding: 0; }
  html, body { width: 1200px; height: 900px; overflow: hidden; }
  body {
    background: radial-gradient(ellipse at 50% 40%, var(--backdrop) 0%, var(--backdrop-edge) 100%);
    font-family: "Arimo", Arial, sans-serif;
    display: flex;
    align-items: center;
    justify-content: center;
    gap: 40px;
  }
  .card {
    width: 540px;
    height: 309px;
    background: var(--card);
    border: 1px solid var(--card-edge);
    box-shadow: 0 18px 40px rgba(0,0,0,0.6);
    display: flex;
    flex-direction: column;
    align-items: center;
    justify-content: center;
    text-align: center;
  }
  /* Rear: services and contact */
  .services { list-style: none; }
  .services li {
    color: var(--text-grey);
    font-size: 14.5px;
    line-height: 1.45;
    letter-spacing: 0.2px;
  }
  .services-rule {
    width: 200px;
    height: 1px;
    background: linear-gradient(90deg, transparent, var(--rule), transparent);
    margin: 14px 0 14px;
  }
  .contact { font-size: 22px; }
  .contact-label { color: var(--accent); }
  .contact-phone { color: var(--text-grey); }
  /* Front: name and tagline */
  .brand-mark { width: 96px; height: 96px; margin-bottom: 18px; }
  .brand-name {
    color: var(--mark-grey);
    font-weight: 700;
    font-size: 27px;
    letter-spacing: 0.5px;
  }
  .brand-rule {
    width: 330px;
    height: 2px;
    background: var(--accent);
    margin: 12px 0 14px;
  }
  .tagline {
    color: var(--accent);
    font-size: 17px;
    letter-spacing: 2.5px;
  }
</style>
</head>
<body>
  <section class="card card-rear">
    <ul class="services">
      <li>Bulk fertilizer including Lime, Gypsum, Manure &amp; Compost</li>
      <li>Granular fertilizer including Single Super, Urea</li>
      <li>Gran-am, &amp; Custom Blends</li>
      <li>Modern equipment</li>
      <li>Autosteer &amp; Variable Rate Capable</li>
      <li>Friendly &amp; Reliable Service</li>
    </ul>
    <div class="services-rule"></div>
    <p class="contact"><span class="contact-label">Contact Gus:</span> <span class="contact-phone">0417 552 308</span></p>
  </section>

  <section class="card card-front">
    <svg class="brand-mark" viewBox="0 0 96 96" aria-hidden="true">
      <circle cx="48" cy="48" r="44" fill="none" stroke="var(--mark-grey)" stroke-width="5"/>
    </svg>
    <h1 class="brand-name">HALLORAN FIELD SERVICES</h1>
    <div class="brand-rule"></div>
    <p class="tagline">CUSTOMISED SPREADING</p>
  </section>
</body>
</html>
```